Website Update for Global Company - Solar Technology - LeafCore

We recently released our first version of our website velirox.com. However despite a longer process of developing the page, it is still missing the elements of a brilliant website. (Currently it looks dead and boring) We are having problems integrating our logo and want to create a more catching site. The task involves an updated and without changing most of main elements in the existing page. (Unless you can do it even better) The blue color needs to be kept but can be changed within the blue-spectrum. The logo text (VELIROX) must be better integrated in the site, however the main logo could be used in elements like we have tried with the background. The surface of the logo could be changed to 3D or metallic, or any other theme that would make the site more complete.
It would be good if some elements of the site could be used on business cards and invoices to keep the company identity.
Velirox is a new development company specialized in green energy and sustainable development. We do design, engineering, manufacturing, sourcing and other processes related to product development – both as consultants and for own products.
Keep the look of the site as professional as possible, and with a cooperate-looking style.

Link to existing page: www.velirox.com

Brief Update : After reviewing the designs we would like all new and current designers to make more bold designs that stands out from the rest. We do not like the standard layout that looks like any other cooperate homepage. We want a very unique and very lively page - with faded images and effects when hoovering like seen on our existing page. Try make all elements blend together, and use faded background images instead of just white color - or something else.

Make the site unique !

Industry/Entity Type

Solar Energy

Contact Information for Business Card

Owner/Founder/CEO : Jonas Ulfkær Lindholm
Company name: Velirox ApS
Email: jonas.ulfkaer@velirox.dk
Phone: +45 71 82 64 93
Slogan Sustainable Development
Address: Kildevej 58, 2
DK-5700 Svendborg, Denmark

Number of Pages Required

3 page

Font styles to use
Serif
Sans Serif

Colors
0555a3
85acd3
cedeed
3176b5
cee9f5
85cae6
0293ce
86cfc6
33b8a4

```html
<!DOCTYPE html>
<html lang="en">
<head>
<meta charset="utf-8">
<title>Velirox – Sustainable Development</title>
<link rel="stylesheet" href="https://fonts.googleapis.com/css2?family=Open+Sans:wght@300;400;600;700&display=swap">
<style>
:root{
  --blue-dark:#0555a3;
  --blue:#3176b5;
  --blue-bright:#0293ce;
  --blue-soft:#85acd3;
  --blue-pale:#cedeed;
  --sky:#85cae6;
  --teal:#33b8a4;
  --ink:#2f3338;
  --muted:#8a8f95;
  --footer:#2a2e33;
  --footer-deep:#1d2024;
  --white:#ffffff;
}
*{box-sizing:border-box;margin:0;padding:0}
html,body{width:686px;height:1200px;overflow:hidden}
body{position:relative;background:#f3f5f7;font-family:"Open Sans",Arial,sans-serif;color:var(--ink)}
.abs{position:absolute}

/* header */
.site-header{left:0;top:0;width:686px;height:50px;background:var(--white)}
.brand{left:112px;top:11px;display:flex;align-items:center;gap:7px}
.brand-mark{width:26px;height:26px;background:var(--blue-dark)}
.brand-name{font-size:19px;font-weight:700;color:var(--blue-dark);letter-spacing:1px}
.header-contact{left:360px;top:18px;font-size:8px;color:var(--muted);display:flex;gap:12px;align-items:center;white-space:nowrap}
.header-contact span{display:flex;align-items:center;gap:4px}
.socials{left:518px;top:17px;display:flex;gap:4px}
.socials i{display:block;width:12px;height:12px;border-radius:50%;border:1px solid #b6bcc3}

/* nav */
.main-nav{left:0;top:50px;width:686px;height:22px;background:linear-gradient(var(--blue),var(--blue-dark));display:flex;padding-left:112px}
.main-nav a{font-size:8px;color:#e4eef8;text-decoration:none;padding:0 18px;line-height:22px}
.main-nav a.active{background:var(--blue-bright);color:var(--white)}

/* hero */
.hero{left:0;top:72px;width:686px;height:260px;overflow:hidden}
.hero-visual{left:0;top:0;width:686px;height:260px;background:
  radial-gradient(ellipse 230px 150px at 210px 120px,rgba(120,160,185,.55) 0%,rgba(120,160,185,0) 100%),
  linear-gradient(180deg,#dfeef2 0%,#cfe7cc 45%,#8cc95a 75%,#5fae33 100%)}
.hero-title{left:370px;top:122px;width:250px;font-size:17px;line-height:21px;font-weight:600;color:var(--white);text-shadow:0 1px 3px rgba(0,60,20,.35)}
.tiles{left:118px;top:282px;width:450px;height:98px;background:var(--white);box-shadow:0 3px 8px rgba(0,0,0,.25);padding:6px;display:flex;gap:6px}
.tile{flex:1;height:86px}
.tile-a{background:linear-gradient(#8a6b52,#3e2c24)}
.tile-b{background:linear-gradient(#8d9aa6,#4d5964)}
.tile-c{background:linear-gradient(#a9c4d8,#3b5e7a)}
.tile-d{background:linear-gradient(#c7cbc8,#6f7b80)}
.tile-labels{left:118px;top:378px;width:450px;height:16px;background:#eef2f5;display:flex;border-top:2px solid var(--blue-bright)}
.tile-labels span{flex:1;text-align:center;font-size:7px;font-weight:600;letter-spacing:.8px;line-height:14px;color:#4f5a64}

/* welcome */
.welcome{left:0;top:396px;width:686px;height:128px;background:linear-gradient(#f6f8f9,#eceff2)}
.welcome h1{position:absolute;left:0;top:30px;width:686px;text-align:center;font-size:15px;font-weight:600;color:#3d434a;letter-spacing:.5px}
.welcome p{position:absolute;left:118px;top:56px;width:450px;text-align:center;font-size:7px;line-height:11px;color:var(--muted)}

/* services */
.services{left:0;top:524px;width:686px;height:264px;background:linear-gradient(180deg,#5a5f63 0%,#2e3236 55%,#1f2226 100%)}
.services h2{position:absolute;left:0;top:28px;width:686px;text-align:center;font-size:20px;font-weight:300;color:var(--white)}
.card{top:78px;width:138px;height:130px}
.card-img{height:82px}
.card-body{height:48px;background:var(--white);padding:6px 8px;position:relative}
.card-body h3{font-size:8px;font-weight:600;color:#3d434a}
.card-body p{font-size:6px;line-height:8px;color:var(--muted);width:96px;margin-top:3px}
.round-btn{position:absolute;right:8px;bottom:10px;width:14px;height:14px;border-radius:50%;border:1px solid #aab1b8}
.img-industrial{background:linear-gradient(#9fb4c4,#4f6372)}
.img-mechanical{background:linear-gradient(#2a6f8c,#0c2a3a)}
.img-electrical{background:linear-gradient(#7e8c83,#2f3a36)}
.slider-arrow{top:160px;width:16px;height:16px}

/* videos & news */
.updates{left:0;top:788px;width:686px;height:215px;background:linear-gradient(#ffffff,#eef1f4)}
.section-label{position:absolute;top:36px;font-size:10px;font-weight:600;color:#3d434a;letter-spacing:.4px}
.video-frame{position:absolute;left:118px;top:56px;width:180px;height:88px;background:linear-gradient(135deg,#d9dde0,#9ba3aa)}
.video-title{position:absolute;left:118px;top:152px;font-size:8px;font-weight:600;color:#3d434a}
.video-text{position:absolute;left:118px;top:164px;width:180px;font-size:6px;line-height:8px;color:var(--muted)}
.news-thumb{position:absolute;left:378px;top:56px;width:52px;height:44px;background:linear-gradient(#b8c2ca,#6c7780)}
.news-date{position:absolute;left:438px;top:56px;font-size:6px;color:var(--blue)}
.news-title{position:absolute;left:438px;top:66px;font-size:7px;font-weight:600;color:#3d434a}
.news-text{position:absolute;left:438px;top:78px;width:130px;font-size:6px;line-height:8px;color:var(--muted)}
.news-more{position:absolute;left:378px;top:106px;width:190px;font-size:6px;line-height:8px;color:var(--muted)}
.btn-more{position:absolute;left:378px;top:136px;width:34px;height:12px;background:var(--blue-bright);color:var(--white);font-size:6px;text-align:center;line-height:12px}
.pager{position:absolute;left:540px;top:136px;display:flex;gap:3px}
.pager i{display:block;width:12px;height:12px;border:1px solid #c2c8ce;background:var(--white)}

/* skyline band */
.skyline{left:0;top:1003px;width:686px;height:67px;background:linear-gradient(#eef1f4 0%,#d6dade 70%,#b9bec3 100%)}

/* footer */
.site-footer{left:0;top:1070px;width:686px;height:112px;background:var(--footer)}
.f-col{position:absolute;top:12px;width:100px}
.f-col h4{font-size:7px;font-weight:600;color:var(--white);margin-bottom:6px}
.f-col li{list-style:none;font-size:6px;line-height:10px;color:#a2a8ae}
.f-contact{font-size:6px;line-height:10px;color:#a2a8ae}
.f-phone{font-size:9px;font-weight:600;color:var(--white);margin-top:4px}
.news-input{width:100px;height:12px;background:#3b4047;margin-top:6px}
.news-btn{width:34px;height:11px;background:var(--blue-bright);margin-top:4px;font-size:6px;color:var(--white);text-align:center;line-height:11px}
.f-social{display:flex;gap:3px;margin-top:6px}
.f-social i{display:block;width:9px;height:9px;background:#565c63;border-radius:2px}
.copyright{left:0;top:1182px;width:686px;height:18px;background:var(--footer-deep);font-size:6px;color:#7f868d;line-height:18px;padding-left:118px}
</style>
</head>
<body>

<header class="site-header abs">
  <div class="brand abs"><div class="brand-mark"></div><div class="brand-name">VELIROX</div></div>
  <div class="header-contact abs">
    <span><svg width="8" height="8" viewBox="0 0 10 10"><path d="M2 1l2 2-1 1.5c.8 1.5 1.8 2.5 3.5 3.5L8 6l2 2-1.5 1.5C5 9 1 5 .5 1.5z" fill="#3176b5"/></svg>+45 71 82 64 93</span>
    <span><svg width="9" height="7" viewBox="0 0 10 8"><rect x=".5" y=".5" width="9" height="7" fill="none" stroke="#3176b5"/><path d="M.5 .5l4.5 4 4.5-4" fill="none" stroke="#3176b5"/></svg>info@velirox.dk</span>
  </div>
  <div class="socials abs"><i></i><i></i><i></i><i></i></div>
</header>

<nav class="main-nav abs">
  <a class="active">Home</a><a>About</a><a>Expertise</a><a>Approach</a><a>Contact</a>
</nav>

<section class="hero abs">
  <div class="hero-visual abs" role="img" aria-label="Photo of a light bulb holding a field of solar panels above green grass"></div>
  <h2 class="hero-title abs">We provide complete Services throughout the product Development Process</h2>
</section>
<div class="tiles abs">
  <div class="tile tile-a" role="img" aria-label="Designer at work"></div>
  <div class="tile tile-b" role="img" aria-label="Engineering sketches"></div>
  <div class="tile tile-c" role="img" aria-label="Solar panel installation"></div>
  <div class="tile tile-d" role="img" aria-label="Workers in a factory hall"></div>
</div>
<div class="tile-labels abs"><span>DESIGN</span><span>ENGINEERING</span><span>SOURCING</span><span>MANUFACTURING</span></div>

<section class="welcome abs">
  <h1>WELCOME TO VELIROX</h1>
  <p>Velirox is a development company focused on green energy and sustainable development. We handle design, engineering, sourcing and manufacturing for new products, working both as consultants for our clients and on our own solar products. Our team follows each project from the first idea and early sketches to tested parts and finished production, keeping quality and cost in balance all the way through.</p>
</section>

<section class="services abs">
  <h2>Our Srvice</h2>
  <svg class="slider-arrow abs" style="left:80px" viewBox="0 0 16 16"><path d="M10 3L5 8l5 5" fill="none" stroke="#fff" stroke-width="1.5"/></svg>
  <svg class="slider-arrow abs" style="left:590px" viewBox="0 0 16 16"><path d="M6 3l5 5-5 5" fill="none" stroke="#fff" stroke-width="1.5"/></svg>
  <div class="card abs" style="left:118px">
    <div class="card-img img-industrial" role="img" aria-label="Industrial plant towers"></div>
    <div class="card-body"><h3>Industrial Design</h3><p>Shaping products that work well and look right from day one.</p><span class="round-btn"></span></div>
  </div>
  <div class="card abs" style="left:274px">
    <div class="card-img img-mechanical" role="img" aria-label="Glowing mechanical gears"></div>
    <div class="card-body"><h3>Mechanical Engineering</h3><p>Robust parts and assemblies built for long service life.</p><span class="round-btn"></span></div>
  </div>
  <div class="card abs" style="left:430px">
    <div class="card-img img-electrical" role="img" aria-label="Printed circuit board"></div>
    <div class="card-body"><h3>Electrical engineering</h3><p>Circuits and control systems for clean energy products.</p><span class="round-btn"></span></div>
  </div>
</section>

<section class="updates abs">
  <div class="section-label" style="left:118px">PROJECT VIDEOS</div>
  <div class="video-frame" role="img" aria-label="Laptop on a desk showing a project video"></div>
  <div class="video-title">Watch our Video</div>
  <p class="video-text">See how our team takes a product from concept to finished production.</p>

  <div class="section-label" style="left:378px">LATEST NEWS</div>
  <div class="news-thumb" role="img" aria-label="Engineer at a workstation"></div>
  <div class="news-date">August 12, 2024</div>
  <div class="news-title">New solar module prototype ready</div>
  <p class="news-text">Our latest module passed its first field tests with strong results in low light.</p>
  <p class="news-more">The prototype will now move into a pilot run with selected partners, and full production is planned for next year.</p>
  <div class="btn-more">more</div>
  <div class="pager"><i></i><i></i></div>
</section>

<div class="skyline abs" role="img" aria-label="Grey silhouettes of wind turbines, factories and power lines"></div>

<footer class="site-footer abs">
  <div class="f-col" style="left:118px"><h4>Main menu</h4><ul><li>Home</li><li>About Velirox</li><li>Expertise</li><li>Contact</li></ul></div>
  <div class="f-col" style="left:228px"><h4>Information</h4><ul><li>Services</li><li>Legal notice</li><li>Terms and conditions</li><li>Privacy policy</li><li>Site map</li></ul></div>
  <div class="f-col" style="left:340px"><h4>Contact us</h4>
    <div class="f-contact">Kildevej 58, 2<br>DK-5700 Svendborg</div>
    <div class="f-phone">+45 71 82 64 93</div>
    <div class="f-contact">jonas.ulfkaer@velirox.dk</div>
  </div>
  <div class="f-col" style="left:460px"><h4>Newsletter</h4>
    <div class="f-contact">Sign up for project news</div>
    <div class="news-input"></div>
    <div class="news-btn">Submit</div>
    <div class="f-social"><i></i><i></i><i></i><i></i><i></i></div>
  </div>
</footer>
<div class="copyright abs">© 2024 Velirox ApS. All rights reserved.</div>

</body>
</html>
```